Business Card Design for Training Business

Clear Path Coaching is a new business that delivers training and other services with a focus on topics related to mental health and wellbeing, for example, Wellmind Response Course, Resilience etc. We have a strong focus on evidence-based psychology and neuroscience. I have a logo which I will upload with the brief, so please consider colours that work well with the logo.
Target Market(s)
Adults, workplaces (particularly government and not-for-profits)
Industry/Entity Type
Business
Contact Information for Business Card
Head Strong TrainingSamantha SellwoodDirector0438 770 517bec@clearpathcoaching.example.auwww.headstrongtraining.com.au

```html
<!DOCTYPE html>
<html lang="en">
<head>
<meta charset="utf-8">
<title>Clear Path Coaching – Business Card</title>
<link rel="stylesheet" href="https://fonts.googleapis.com/css2?family=Raleway:wght@200&family=Roboto+Condensed:wght@300&family=Jost:wght@400&display=swap">
<style>
  :root {
    --page: #ffffff;
    --card: #000000;
    --frame: #1c9fd6;
    --teal: #00b0bb;
    --teal-line: #3cb6bd;
    --slate: #727071;
    --white: #ffffff;
    --soft-white: #d8d8d8;
    --web-grey: #6d6d6d;
  }
  * { margin: 0; padding: 0; box-sizing: border-box; }
  html, body {
    width: 1200px;
    height: 740px;
    overflow: hidden;
    background: var(--page);
  }
  .card {
    position: relative;
    width: 1200px;
    height: 740px;
  }
  .card__body {
    position: absolute;
    left: 18px; top: 18px;
    width: 1164px; height: 704px;
    background: var(--card);
  }
  .card__frame {
    position: absolute;
    left: 44px; top: 44px;
    width: 1114px; height: 652px;
    border: 2px solid var(--frame);
  }
  .brand {
    position: absolute;
    right: 478px;
    top: 190px;
    text-align: right;
    font-family: "Raleway", sans-serif;
    font-weight: 200;
    color: var(--white);
  }
  .brand__name {
    display: block;
    font-size: 68px;
    line-height: 1;
    letter-spacing: 4px;
    white-space: nowrap;
  }
  .brand__sub {
    display: block;
    margin-top: 18px;
    font-size: 30px;
    line-height: 1;
    letter-spacing: 17px;
    margin-right: -17px;
    color: var(--soft-white);
    white-space: nowrap;
  }
  .brand__mark {
    position: absolute;
    left: 746px; top: 121px;
  }
  .person {
    position: absolute;
    left: 18px; top: 403px;
    width: 577px; height: 187px;
    background: var(--slate);
    color: var(--white);
    text-align: center;
    padding-left: 20px;
  }
  .person__name {
    margin-top: 57px;
    font-family: "Roboto Condensed", sans-serif;
    font-weight: 300;
    font-size: 44px;
    line-height: 1;
    letter-spacing: 3px;
    white-space: nowrap;
  }
  .person__role {
    margin-top: 10px;
    font-family: "Jost", sans-serif;
    font-size: 27px;
    line-height: 1;
    letter-spacing: 3px;
  }
  .contact {
    position: absolute;
    left: 607px; top: 403px;
    width: 575px; height: 187px;
    background: var(--teal);
    list-style: none;
    padding: 38px 0 0 26px;
    overflow: hidden;
  }
  .contact__item {
    display: flex;
    align-items: center;
    height: 39px;
    font-family: "Roboto Condensed", sans-serif;
    font-weight: 300;
    font-size: 24px;
    letter-spacing: -0.3px;
    white-space: nowrap;
    color: var(--white);
  }
  .contact__icon {
    width: 28px; height: 28px;
    margin-right: 16px;
    flex: none;
  }
  .web-strip {
    position: absolute;
    left: 18px; top: 603px;
    width: 1164px; height: 39px;
    background: var(--page);
    font-family: "Jost", sans-serif;
    font-size: 21px;
    line-height: 39px;
    padding-left: 107px;
    color: var(--web-grey);
    white-space: nowrap;
  }
</style>
</head>
<body>
<div class="card">
  <div class="card__body"></div>
  <div class="card__frame"></div>

  <div class="brand">
    <span class="brand__name">CLEAR PATH</span>
    <span class="brand__sub">COACHING</span>
  </div>
  <svg class="brand__mark" width="254" height="254" viewBox="0 0 254 254" aria-hidden="true">
    <circle cx="127" cy="127" r="125" fill="none" stroke="var(--teal-line)" stroke-width="3"/>
  </svg>

  <div class="person">
    <p class="person__name">REBECCA TANFIELD</p>
    <p class="person__role">Director</p>
  </div>

  <ul class="contact">
    <li class="contact__item">
      <svg class="contact__icon" viewBox="0 0 28 28" aria-hidden="true">
        <circle cx="14" cy="14" r="14" fill="var(--white)"/>
        <path d="M14 6a5.5 5.5 0 0 0-5.5 5.5c0 4 5.5 10.5 5.5 10.5s5.5-6.5 5.5-10.5A5.5 5.5 0 0 0 14 6z" fill="var(--teal)"/>
        <circle cx="14" cy="11.5" r="2.2" fill="var(--white)"/>
      </svg>
      27 Harbour Lane, Kent Street, Fairbridge, F14 K286
    </li>
    <li class="contact__item">
      <svg class="contact__icon" viewBox="0 0 28 28" aria-hidden="true">
        <circle cx="14" cy="14" r="14" fill="var(--white)"/>
        <path d="M9.5 6.5l3 3.5-1.8 2c.9 2 2.4 3.6 4.5 4.6l2-1.8 3.4 3-1.6 2.6c-6 -.4-11.4-5.8-11.6-11.8z" fill="var(--teal)"/>
      </svg>
      +353 1 586 2093
    </li>
    <li class="contact__item">
      <svg class="contact__icon" viewBox="0 0 28 28" aria-hidden="true">
        <circle cx="14" cy="14" r="14" fill="var(--white)"/>
        <rect x="6.5" y="9" width="15" height="10.5" fill="none" stroke="var(--teal)" stroke-width="1.6"/>
        <path d="M6.5 9l7.5 6 7.5-6" fill="none" stroke="var(--teal)" stroke-width="1.6"/>
      </svg>
      517bec@clearpathcoaching.example
    </li>
  </ul>

  <div class="web-strip">www.clearpathcoaching.example.au</div>
</div>
</body>
</html>
```